Brightfield Ventures Inc. Letterhead

Creation of attractive and eye catching letterhead for a business start-up for the construction industry. Letterhead must relate to construction, but avoid standard hammer and tools in the design.

I forgot to add some details, sorry about that. Some pertinent info: Ph: 916-555-0187 brightfieldventures.example 448 Willowmere Ave, Ste 210 Folsom, CA 95999 info@brightfieldventures.example not sure if slogan should be in there" “Connecting construction professionals to create a purpose driven industry.” must be able to be used in word. Thanks!

```html
<!DOCTYPE html>
<html lang="en">
<head>
<meta charset="utf-8">
<title>Brightfield Ventures Inc. Letterhead</title>
<link rel="stylesheet" href="https://fonts.googleapis.com/css2?family=Montserrat:wght@500;600&family=Nunito+Sans:wght@400&display=swap">
<style>
  :root {
    --backdrop: #d9cbb1;
    --paper: #ffffff;
    --navy: #1d2259;
    --red: #c0232c;
    --ink: #3a3a3a;
  }
  html, body {
    margin: 0;
    width: 1200px;
    height: 898px;
    overflow: hidden;
    background: var(--backdrop);
  }
  .letterhead {
    position: absolute;
    left: 296px;
    top: 19px;
    width: 608px;
    height: 860px;
    background: var(--paper);
    box-shadow: 0 6px 24px rgba(60, 45, 20, 0.18);
  }
  .edge-stripe {
    position: absolute;
    top: 0;
    bottom: 0;
    width: 8px;
  }
  .edge-stripe--red { left: 12px; background: var(--red); }
  .edge-stripe--navy { left: 25px; background: var(--navy); }

  .brand {
    position: absolute;
    left: 72px;
    top: 56px;
    display: flex;
    align-items: center;
    gap: 8px;
    font-family: "Montserrat", sans-serif;
    font-weight: 600;
    font-size: 15px;
    letter-spacing: 0.06em;
    text-transform: uppercase;
    color: var(--navy);
  }
  .brand__mark {
    width: 10px;
    height: 10px;
    background: var(--red);
  }

  .letter-body {
    position: absolute;
    left: 96px;
    top: 168px;
    width: 432px;
    font-family: "Nunito Sans", sans-serif;
    font-size: 10.5px;
    line-height: 1.45;
    color: var(--ink);
  }
  .letter-body p {
    margin: 0 0 14px;
    text-align: justify;
  }
  .letter-body .salutation { margin-bottom: 12px; }
  .letter-body .closing { margin-top: 56px; }

  .contact-list {
    position: absolute;
    left: 92px;
    top: 714px;
    margin: 0;
    padding: 0;
    list-style: none;
    font-family: "Montserrat", sans-serif;
    font-weight: 500;
    font-size: 13px;
    line-height: 1.35;
    color: var(--navy);
  }
  .contact-list li {
    display: flex;
    align-items: flex-start;
    gap: 10px;
    margin-bottom: 6px;
  }
  .contact-list svg {
    flex: none;
    width: 12px;
    height: 12px;
    margin-top: 3px;
  }
</style>
</head>
<body>
  <main class="letterhead">
    <div class="edge-stripe edge-stripe--red"></div>
    <div class="edge-stripe edge-stripe--navy"></div>

    <header class="brand">
      <span class="brand__mark"></span>
      <span class="brand__name">Brightfield Ventures</span>
    </header>

    <section class="letter-body">
      <p class="salutation">Dear :</p>
      <p>Lorem ipsum dolor sit amet, consectetur adipiscing elit. Aenean ut ipsum eget massa hendrerit vestibulum vel in velit. Donec pretium neque velit.</p>
      <p>Aliquam porta lectus nec mauris ornare venenatis. Vivamus non est turpis, et cursus sem. Mauris vehicula erat in diam auctor at bibendum nisl lacinia.</p>
      <p>Morbi imperdiet neque vehicula nunc convallis gravida. Vestibulum iaculis pretium placerat. Integer consequat, est sit amet facilisis eleifend, nibh nibh varius orci, eget dapibus arcu dui non purus. Pellentesque in magna mauris. Duis enim sapien, dictum vitae condimentum a, pulvinar vel lacus. Mauris et molestie nibh. Vestibulum vitae nulla at metus elementum porta sit amet interdum elit. Nulla sollicitudin neque eu nulla volutpat congue.</p>
      <p>Etiam pellentesque, velit id dapibus fermentum, turpis sapien ornare dui, ac tincidunt ligula odio congue purus. Nunc sed ante dui, in porta lectus. Cras nec sem lorem. In hac habitasse platea dictumst. Maecenas id diam quis dui porta tristique. Sed id egestas felis. Donec ullamcorper mattis posuere. Phasellus fermentum eleifend tortor vel dapibus. Vestibulum ante ipsum.</p>
      <p>Etiam pellentesque, velit id dapibus fermentum, turpis sapien ornare dui, ac tincidunt ligula odio congue purus. Nunc sed ante dui, in porta lectus. Cras nec sem lorem. In hac habitasse platea dictumst. Maecenas id diam quis dui porta tristique. Sed id egestas felis. Donec ullamcorper mattis posuere. Phasellus fermentum eleifend tortor vel dapibus. Vestibulum ante ipsum.</p>
      <p class="closing">Sincerely,</p>
    </section>

    <ul class="contact-list">
      <li>
        <svg viewBox="0 0 12 12" aria-hidden="true"><circle cx="6" cy="6" r="6" fill="var(--navy)"/><path d="M4 3.2 5 4.6 4.5 5.3c.4.9 1.2 1.7 2.1 2.1l.7-.5 1.4 1-.5 1c-2.4-.3-4.4-2.3-4.7-4.7z" fill="#fff"/></svg>
        <span>916-555-0187</span>
      </li>
      <li>
        <svg viewBox="0 0 12 12" aria-hidden="true"><circle cx="6" cy="6" r="6" fill="var(--navy)"/><rect x="3" y="4" width="6" height="4.2" fill="#fff"/><path d="M3 4 6 6.4 9 4" stroke="var(--navy)" stroke-width=".7" fill="none"/></svg>
        <span>info@brightfieldventures.example</span>
      </li>
      <li>
        <svg viewBox="0 0 12 12" aria-hidden="true"><circle cx="6" cy="6" r="6" fill="var(--navy)"/><circle cx="6" cy="6" r="3.3" stroke="#fff" stroke-width=".8" fill="none"/><path d="M2.7 6h6.6M6 2.7c-1.6 2-1.6 4.6 0 6.6M6 2.7c1.6 2 1.6 4.6 0 6.6" stroke="#fff" stroke-width=".7" fill="none"/></svg>
        <span>brightfieldventures.example</span>
      </li>
      <li>
        <svg viewBox="0 0 12 12" aria-hidden="true"><circle cx="6" cy="6" r="6" fill="var(--navy)"/><path d="M6 2.6a2.3 2.3 0 0 0-2.3 2.3C3.7 6.7 6 9.4 6 9.4s2.3-2.7 2.3-4.5A2.3 2.3 0 0 0 6 2.6z" fill="#fff"/><circle cx="6" cy="4.9" r=".8" fill="var(--navy)"/></svg>
        <span>448 Willowmere Ave,<br>Ste 210 Folsom, CA 95999</span>
      </li>
    </ul>
  </main>
</body>
</html>
```